Real Estate Webpage Design

We have an existing website: ferndaleestatecollective.com.au
We focus customised service mainly on Property Management and second-hand property sales.
We are not entirely happy about the current design and layout can stay roughly the same as the back end coding is linked to a CRM system.
We would like to see the design are more reachable to our clients and appearing.
Please check our Website Design Draft for more details.

Industry/Entity Type

Real estate Agency

Number of Pages Required

5+ page

Font styles to use
Sans Serif

Colors

Designer to choose colors to be used in the design.

```html
<!DOCTYPE html>
<html lang="en">
<head>
<meta charset="utf-8">
<title>Ferndale Property Group</title>
<link href="https://fonts.googleapis.com/css2?family=Exo+2:wght@600;700&family=Roboto:wght@400;500;700&display=swap" rel="stylesheet">
<style>
:root{
  --orange:#f6a623;
  --orange-dark:#e8951a;
  --navy:#22252e;
  --ink:#222;
  --text:#666;
  --muted:#8a8a8a;
  --line:#eee;
  --white:#fff;
}
*{box-sizing:border-box;margin:0;padding:0}
html,body{width:1200px;height:4525px;overflow:hidden}
body{font-family:"Roboto",sans-serif;color:var(--ink);background:var(--white);position:relative}
.abs{position:absolute}
svg{display:block}
/* header */
.site-header{position:absolute;left:0;top:0;width:1200px;height:92px;background:var(--white);z-index:3}
.brand{position:absolute;left:110px;top:16px;display:flex;align-items:center;gap:12px}
.brand-mark{width:40px;height:40px;background:var(--orange)}
.brand-name{font-family:"Exo 2",sans-serif;font-weight:700;font-size:34px;color:var(--orange);line-height:1}
.brand-sub{font-size:11px;color:var(--orange);margin-top:3px}
.topbar{position:absolute;left:460px;top:10px;height:34px;display:flex;align-items:center;gap:10px;font-size:15px;color:#333}
.circle-ic{width:30px;height:30px;border:1.5px solid #333;border-radius:50%;display:flex;align-items:center;justify-content:center}
.topbar .phone{font-weight:700}
.topbar .sep{width:1px;height:22px;background:#333;margin:0 4px}
.soc{width:28px;height:28px;border:1.5px solid #333;border-radius:50%}
.main-nav{position:absolute;left:405px;top:52px;width:795px;height:40px;background:var(--navy);display:flex;align-items:center;padding-left:30px;gap:34px}
.main-nav a{color:#fff;text-decoration:none;font-size:15px;font-weight:500}
/* hero */
.hero{position:absolute;left:0;top:92px;width:1200px;height:630px;background:linear-gradient(180deg,#c9a677 0%,#7a8ea3 35%,#3c5f80 65%,#2a4866 100%);text-align:center}
.hero h1{position:absolute;top:170px;width:100%;font-family:"Exo 2",sans-serif;font-weight:700;font-size:60px;color:#fff;letter-spacing:1px}
.hero p{position:absolute;top:252px;left:300px;width:600px;color:#fff;font-size:16px;line-height:27px}
.btn{display:inline-flex;align-items:center;gap:8px;background:var(--orange);color:#fff;font-weight:700;text-decoration:none;border-radius:26px;text-transform:uppercase}
.hero .btn{position:absolute;top:333px;left:494px;height:52px;padding:0 38px;font-size:16px}
.hero-edge{position:absolute;left:0;top:640px;z-index:2}
/* about */
.about-photo{left:110px;top:816px;width:450px;height:450px;background:linear-gradient(135deg,#c7d2dc,#9aa6ad 50%,#4d6b5a)}
.about-text{left:640px;top:852px;width:455px}
.sec-title{font-family:"Exo 2",sans-serif;font-weight:700;color:var(--navy);text-transform:uppercase}
.sec-title span{color:var(--orange)}
.about-text h2{font-size:31px;margin-bottom:24px}
.about-text p{font-size:14px;line-height:26.5px;color:var(--text);margin-bottom:12px}
.about-text .btn{margin-top:30px;height:44px;padding:0 30px;font-size:15px}
/* services */
.services{left:0;top:1392px;width:1200px;height:253px;display:flex}
.service{flex:1;display:flex;flex-direction:column;align-items:center;padding-top:58px;background:linear-gradient(180deg,#2b2f38,#1f222a)}
.service.featured{background:var(--orange)}
.service .ic{width:100px;height:100px;border-radius:50%;background:var(--orange);border:3px solid #fff;display:flex;align-items:center;justify-content:center}
.service.featured .ic{background:var(--navy)}
.service h3{margin-top:24px;color:#fff;font-size:21px;font-weight:700}
/* properties */
.centered{width:1200px;text-align:center;left:0}
.prop-title{top:1730px;font-size:40px}
.card{position:absolute;width:313px;background:#fff;box-shadow:0 4px 14px rgba(0,0,0,.12)}
.prop .pic{height:193px;position:relative}
.badge{position:absolute;right:10px;top:14px;background:var(--orange);color:#fff;font-size:15px;padding:3px 14px;font-weight:500}
.prop h4{font-size:16px;font-weight:700;margin:16px 0 0 15px;color:#222}
.addr{font-size:12px;color:var(--muted);margin:6px 0 0 15px;display:flex;gap:6px;align-items:center}
.feats{display:grid;grid-template-columns:150px 150px;row-gap:16px;margin:22px 0 0 15px;font-size:13px;color:#666}
.feats div{display:flex;align-items:center;gap:12px}
.prop .btn{position:absolute;left:85px;bottom:-22px;height:44px;padding:0 22px;border-radius:0;font-size:15px}
/* testimonials */
.city{left:0;top:2670px;width:1200px;height:316px;background:linear-gradient(180deg,#eef0f2 0%,#b8c0c6 45%,#5c6a6a 80%,#3f4a43 100%)}
.testimonials{left:0;top:2986px;width:1200px;height:456px;background:var(--orange)}
.testimonials h2{position:absolute;top:66px;width:100%;text-align:center;font-family:"Exo 2",sans-serif;font-weight:700;font-size:38px;color:#fff}
.quote-card{position:absolute;top:146px;width:408px;height:230px;background:#fff;border-radius:40px;box-shadow:0 6px 14px rgba(0,0,0,.15)}
.avatar{position:absolute;left:-50px;top:58px;width:112px;height:112px;border-radius:50%;background:linear-gradient(180deg,#9a8f86,#4a4f5a);border:4px solid #fff}
.quote-card .qm{position:absolute;left:100px;top:26px}
.quote-card p{position:absolute;left:100px;top:74px;width:275px;font-size:14px;line-height:23px;color:#666}
.quote-card h5{position:absolute;left:100px;top:160px;font-size:16px;font-weight:700}
.quote-card .stars{position:absolute;left:100px;top:183px;display:flex;gap:3px}
.arrow{position:absolute;top:248px}
/* blog */
.blog-title{top:3508px;font-size:40px}
.post{top:3585px;height:386px;padding:8px;text-align:center}
.post .pic{height:202px}
.post .date{margin-top:32px;font-size:14px;color:#333;display:flex;gap:8px;justify-content:center;align-items:center}
.post h4{font-size:17px;font-weight:700;margin-top:10px}
.post p{font-size:14px;color:#777;line-height:22px;margin:14px 14px 0}
.readmore{display:inline-flex;align-items:center;gap:7px;margin-top:16px;color:var(--orange);font-weight:700;font-size:15px}
/* footer */
.footer{left:0;top:4085px;width:1200px;height:385px;background:var(--navy)}
.footer-edge{position:absolute;left:0;top:0}
.fcol{position:absolute;top:127px;color:#fff}
.fcol h6{font-size:18px;font-weight:700;margin-bottom:22px;text-transform:uppercase}
.fcol ul{list-style:none}
.fcol li{font-size:12px;color:#ddd;line-height:26px;padding-left:6px}
.contact li{display:flex;gap:16px;align-items:flex-start;margin-bottom:12px;line-height:18px;padding-left:4px}
.fcol .lead{font-size:12px;color:#ddd;line-height:20px;width:240px;padding-left:6px}
.sub-form{margin:16px 0 0 6px;width:250px;height:36px;background:#fff;border-radius:18px;display:flex;align-items:center;justify-content:space-between;padding-left:12px;font-size:11px;color:#666}
.sub-form .go{width:46px;height:36px;background:var(--orange);border-radius:0 18px 18px 0;display:flex;align-items:center;justify-content:center}
.fsoc{display:flex;gap:10px;margin:16px 0 0 6px}
.fsoc span{width:30px;height:30px;border-radius:50%;background:#fff}
.fsoc span.o{background:var(--orange)}
.bottom-bar{left:0;top:4470px;width:1200px;height:55px;background:var(--navy);border-top:1px solid #3a3e48;color:#fff;font-size:13px}
.bottom-bar .l{position:absolute;left:110px;top:20px}
.bottom-bar .l u{margin:0 4px}
.bottom-bar .r{position:absolute;right:112px;top:20px}
</style>
</head>
<body>

<header class="site-header">
  <div class="brand">
    <div class="brand-mark"></div>
    <div><div class="brand-name">Ferndale</div><div class="brand-sub">Property Group</div></div>
  </div>
  <div class="topbar">
    <span>Talk To Us Today</span>
    <span class="circle-ic"><svg width="14" height="14" viewBox="0 0 24 24"><path d="M6.6 10.8a15 15 0 006.6 6.6l2.2-2.2a1 1 0 011-.25 11.4 11.4 0 003.6.57 1 1 0 011 1V20a1 1 0 01-1 1A17 17 0 013 4a1 1 0 011-1h3.5a1 1 0 011 1 11.4 11.4 0 00.57 3.6 1 1 0 01-.25 1z" fill="#333"/></svg></span>
    <span class="phone">188-555-0142</span>
    <svg width="14" height="14" viewBox="0 0 24 24" style="margin-left:12px"><circle cx="10" cy="10" r="7" stroke="#333" stroke-width="3" fill="none"/><path d="M15 15l6 6" stroke="#333" stroke-width="3"/></svg>
    <span class="sep"></span>
    <span class="circle-ic"><svg width="14" height="14" viewBox="0 0 24 24"><circle cx="12" cy="8" r="4.5" fill="#333"/><path d="M3 22a9 9 0 0118 0z" fill="#333"/></svg></span>
    <span>My Account</span>
    <span class="sep"></span>
    <span class="soc"></span><span class="soc"></span><span class="soc"></span>
  </div>
  <nav class="main-nav">
    <a href="#">Home</a><a href="#">About Us</a><a href="#">Leasing</a><a href="#">Buy</a><a href="#">Sell</a><a href="#">Our Team</a><a href="#">Blog</a><a href="#">Contact Us</a>
  </nav>
</header>

<section class="hero" role="img" aria-label="Harbour city skyline with bridge and boats at sunset">
  <h1>FERNDALE</h1>
  <p>Ferndale in Spanish means “the home, the house”, buying a property is one of the most expensive expenses and important assets for people.</p>
  <a class="btn" href="#">Get Started
    <svg width="16" height="16" viewBox="0 0 24 24"><circle cx="12" cy="12" r="11" fill="#fff"/><path d="M10 7l5 5-5 5" stroke="#f6a623" stroke-width="3" fill="none"/></svg></a>
</section>
<svg class="hero-edge" width="1200" height="82" viewBox="0 0 1200 82">
  <polygon points="0,82 0,72 300,18 600,72 900,18 1200,72 1200,82" fill="#fff"/>
  <polygon points="80,66 300,28 520,66 300,42" fill="#f6a623"/>
  <polygon points="680,66 900,28 1120,66 900,42" fill="#f6a623"/>
</svg>

<div class="abs about-photo" role="img" aria-label="Collage of modern home interiors and garden"></div>
<div class="abs about-text">
  <h2 class="sec-title">Spanish for <span>“The Home”</span></h2>
  <p>Ferndale in Spanish means “the home, the house”, buying a property is one of the most expensive expenses and important assets for people. Ferndale is a real estate company located in Gungahlin, Canberra.</p>
  <p>Being a portfolio sales agent and property manager, coupled with our high–profile international real estate experience, Ferndale is considered a market leader on the cutting edge with deep industry knowledge, ranging from landlord–tenant relationships, residential purchases.</p>
  <a class="btn" href="#">Learn More
    <svg width="14" height="14" viewBox="0 0 24 24"><circle cx="12" cy="12" r="11" fill="#fff"/><path d="M10 7l5 5-5 5" stroke="#f6a623" stroke-width="3" fill="none"/></svg></a>
</div>

<section class="abs services">
  <div class="service">
    <div class="ic"><svg width="54" height="54" viewBox="0 0 54 54" fill="none" stroke="#fff" stroke-width="3"><path d="M6 26L27 8l21 18"/><path d="M12 22v24h30V22"/><rect x="17" y="28" width="20" height="10"/></svg></div>
    <h3>LEASING</h3>
  </div>
  <div class="service featured">
    <div class="ic"><svg width="54" height="54" viewBox="0 0 54 54" fill="none" stroke="#fff" stroke-width="3"><circle cx="20" cy="16" r="7"/><path d="M26 20l14 14M34 28l4-4M38 32l3-3"/><path d="M8 44h12l10-6h12"/></svg></div>
    <h3>BUY</h3>
  </div>
  <div class="service">
    <div class="ic"><svg width="54" height="54" viewBox="0 0 54 54" fill="none" stroke="#fff" stroke-width="3"><path d="M8 24l10-8 10 6 8-6 10 8"/><path d="M14 30l8 8 6-4 6 4 8-8"/><path d="M27 12v8"/></svg></div>
    <h3>SELL</h3>
  </div>
</section>

<h2 class="abs centered sec-title prop-title">Ferndale <span>Property</span></h2>

<!-- property card template repeated -->
<div class="card prop" style="left:110px;top:1822px;height:378px">
  <div class="pic" role="img" aria-label="Rooftop infinity pool beside apartment towers" style="background:linear-gradient(135deg,#b9c7d3,#6f8fa8 55%,#34526a)"><span class="badge">Buy</span></div>
  <h4>Amazing apartment with ultra</h4>
  <div class="addr"><svg width="10" height="13" viewBox="0 0 10 14"><path d="M5 0a5 5 0 015 5c0 4-5 9-5 9S0 9 0 5a5 5 0 015-5z" fill="#f6a623"/><circle cx="5" cy="5" r="2" fill="#fff"/></svg>Level 5/18 Wattle Grove Avenue</div>
  <div class="feats">
    <div><svg width="18" height="14" viewBox="0 0 18 14" fill="none" stroke="#f6a623" stroke-width="1.5"><path d="M1 1v12M1 9h16v4M4 6h12v3"/></svg>2 Bed Rooms</div>
    <div><svg width="18" height="14" viewBox="0 0 18 14" fill="none" stroke="#f6a623" stroke-width="1.5"><path d="M1 7h16v2a4 4 0 01-4 4H5a4 4 0 01-4-4zM4 7V2a1.5 1.5 0 013 0"/></svg>2 Bath Rooms</div>
    <div><svg width="18" height="14" viewBox="0 0 18 14" fill="none" stroke="#f6a623" stroke-width="1.5"><rect x="1" y="1" width="16" height="12"/><path d="M1 10l5-4 4 3 3-2 4 3"/></svg>38 Pictures</div>
    <div><svg width="18" height="14" viewBox="0 0 18 14" fill="none" stroke="#f6a623" stroke-width="1.5"><rect x="1" y="1" width="16" height="12"/><path d="M5 5h8v5H5z"/></svg>2513 Sqft</div>
  </div>
  <a class="btn" href="#">Learn More</a>
</div>

<div class="card prop" style="left:443px;top:1822px;height:378px">
  <div class="pic" role="img" aria-label="Backyard swimming pool with shade sails" style="background:linear-gradient(160deg,#cfd8dc,#6e9fb3 50%,#2c4fa3)"><span class="badge">Buy</span></div>
  <h4>Amazing apartment with ultra</h4>
  <div class="addr"><svg width="10" height="13" viewBox="0 0 10 14"><path d="M5 0a5 5 0 015 5c0 4-5 9-5 9S0 9 0 5a5 5 0 015-5z" fill="#f6a623"/><circle cx="5" cy="5" r="2" fill="#fff"/></svg>Level 5/18 Wattle Grove Avenue</div>
  <div class="feats">
    <div><svg width="18" height="14" viewBox="0 0 18 14" fill="none" stroke="#f6a623" stroke-width="1.5"><path d="M1 1v12M1 9h16v4M4 6h12v3"/></svg>2 Bed Rooms</div>
    <div><svg width="18" height="14" viewBox="0 0 18 14" fill="none" stroke="#f6a623" stroke-width="1.5"><path d="M1 7h16v2a4 4 0 01-4 4H5a4 4 0 01-4-4zM4 7V2a1.5 1.5 0 013 0"/></svg>2 Bath Rooms</div>
    <div><svg width="18" height="14" viewBox="0 0 18 14" fill="none" stroke="#f6a623" stroke-width="1.5"><rect x="1" y="1" width="16" height="12"/><path d="M1 10l5-4 4 3 3-2 4 3"/></svg>38 Pictures</div>
    <div><svg width="18" height="14" viewBox="0 0 18 14" fill="none" stroke="#f6a623" stroke-width="1.5"><rect x="1" y="1" width="16" height="12"/><path d="M5 5h8v5H5z"/></svg>2513 Sqft</div>
  </div>
  <a class="btn" href="#">Learn More</a>
</div>

<div class="card prop" style="left:775px;top:1822px;height:378px">
  <div class="pic" role="img" aria-label="Renovated family house with double garage" style="background:linear-gradient(180deg,#5f8fd0,#c8c3bb 55%,#8a7a6a)"><span class="badge">Lease</span></div>
  <h4>A newly- renovated idyllic 4-bedroom</h4>
  <div class="addr"><svg width="10" height="13" viewBox="0 0 10 14"><path d="M5 0a5 5 0 015 5c0 4-5 9-5 9S0 9 0 5a5 5 0 015-5z" fill="#f6a623"/><circle cx="5" cy="5" r="2" fill="#fff"/></svg>9 Kestrel Street Red Hill ACT</div>
  <div class="feats">
    <div><svg width="18" height="14" viewBox="0 0 18 14" fill="none" stroke="#f6a623" stroke-width="1.5"><path d="M1 1v12M1 9h16v4M4 6h12v3"/></svg>2 Bed Rooms</div>
    <div><svg width="18" height="14" viewBox="0 0 18 14" fill="none" stroke="#f6a623" stroke-width="1.5"><path d="M1 7h16v2a4 4 0 01-4 4H5a4 4 0 01-4-4zM4 7V2a1.5 1.5 0 013 0"/></svg>2 Bath Rooms</div>
    <div><svg width="18" height="14" viewBox="0 0 18 14" fill="none" stroke="#f6a623" stroke-width="1.5"><rect x="1" y="1" width="16" height="12"/><path d="M1 10l5-4 4 3 3-2 4 3"/></svg>38 Pictures</div>
    <div><svg width="18" height="14" viewBox="0 0 18 14" fill="none" stroke="#f6a623" stroke-width="1.5"><rect x="1" y="1" width="16" height="12"/><path d="M5 5h8v5H5z"/></svg>2513 Sqft</div>
  </div>
  <a class="btn" href="#">Learn More</a>
</div>

<div class="card prop" style="left:110px;top:2277px;height:378px">
  <div class="pic" role="img" aria-label="Bright living room with grey sofa" style="background:linear-gradient(135deg,#e8e6e2,#c9c4bc 55%,#8e8780)"><span class="badge">Sell</span></div>
  <h4>Modern home in contemporary style</h4>
  <div class="addr"><svg width="10" height="13" viewBox="0 0 10 14"><path d="M5 0a5 5 0 015 5c0 4-5 9-5 9S0 9 0 5a5 5 0 015-5z" fill="#f6a623"/><circle cx="5" cy="5" r="2" fill="#fff"/></svg>35/12 Banksia Drive Moncrieff ACT</div>
  <div class="feats">
    <div><svg width="18" height="14" viewBox="0 0 18 14" fill="none" stroke="#f6a623" stroke-width="1.5"><path d="M1 1v12M1 9h16v4M4 6h12v3"/></svg>2 Bed Rooms</div>
    <div><svg width="18" height="14" viewBox="0 0 18 14" fill="none" stroke="#f6a623" stroke-width="1.5"><path d="M1 7h16v2a4 4 0 01-4 4H5a4 4 0 01-4-4zM4 7V2a1.5 1.5 0 013 0"/></svg>2 Bath Rooms</div>
    <div><svg width="18" height="14" viewBox="0 0 18 14" fill="none" stroke="#f6a623" stroke-width="1.5"><rect x="1" y="1" width="16" height="12"/><path d="M1 10l5-4 4 3 3-2 4 3"/></svg>38 Pictures</div>
    <div><svg width="18" height="14" viewBox="0 0 18 14" fill="none" stroke="#f6a623" stroke-width="1.5"><rect x="1" y="1" width="16" height="12"/><path d="M5 5h8v5H5z"/></svg>2513 Sqft</div>
  </div>
  <a class="btn" href="#">Learn More</a>
</div>

<div class="card prop" style="left:443px;top:2277px;height:378px">
  <div class="pic" role="img" aria-label="Apartment lounge with city view windows" style="background:linear-gradient(135deg,#7b8590,#4c4a4a 55%,#6b4a30)"><span class="badge">Lease</span></div>
  <h4>A cosmopolitan lifestyle you desire.</h4>
  <div class="addr"><svg width="10" height="13" viewBox="0 0 10 14"><path d="M5 0a5 5 0 015 5c0 4-5 9-5 9S0 9 0 5a5 5 0 015-5z" fill="#f6a623"/><circle cx="5" cy="5" r="2" fill="#fff"/></svg>215/2 Lantern Street Braddon ACT</div>
  <div class="feats">
    <div><svg width="18" height="14" viewBox="0 0 18 14" fill="none" stroke="#f6a623" stroke-width="1.5"><path d="M1 1v12M1 9h16v4M4 6h12v3"/></svg>2 Bed Rooms</div>
    <div><svg width="18" height="14" viewBox="0 0 18 14" fill="none" stroke="#f6a623" stroke-width="1.5"><path d="M1 7h16v2a4 4 0 01-4 4H5a4 4 0 01-4-4zM4 7V2a1.5 1.5 0 013 0"/></svg>2 Bath Rooms</div>
    <div><svg width="18" height="14" viewBox="0 0 18 14" fill="none" stroke="#f6a623" stroke-width="1.5"><rect x="1" y="1" width="16" height="12"/><path d="M1 10l5-4 4 3 3-2 4 3"/></svg>38 Pictures</div>
    <div><svg width="18" height="14" viewBox="0 0 18 14" fill="none" stroke="#f6a623" stroke-width="1.5"><rect x="1" y="1" width="16" height="12"/><path d="M5 5h8v5H5z"/></svg>2513 Sqft</div>
  </div>
  <a class="btn" href="#">Learn More</a>
</div>

<div class="card prop" style="left:775px;top:2277px;height:378px">
  <div class="pic" role="img" aria-label="Aerial view of a suburban family home" style="background:linear-gradient(180deg,#a9c1dc,#8d9a8a 55%,#5d7050)"><span class="badge">Sell</span></div>
  <h4>An idyllic family home with peace</h4>
  <div class="addr"><svg width="10" height="13" viewBox="0 0 10 14"><path d="M5 0a5 5 0 015 5c0 4-5 9-5 9S0 9 0 5a5 5 0 015-5z" fill="#f6a623"/><circle cx="5" cy="5" r="2" fill="#fff"/></svg>25 Myrtle Close Bonner ACT</div>
  <div class="feats">
    <div><svg width="18" height="14" viewBox="0 0 18 14" fill="none" stroke="#f6a623" stroke-width="1.5"><path d="M1 1v12M1 9h16v4M4 6h12v3"/></svg>2 Bed Rooms</div>
    <div><svg width="18" height="14" viewBox="0 0 18 14" fill="none" stroke="#f6a623" stroke-width="1.5"><path d="M1 7h16v2a4 4 0 01-4 4H5a4 4 0 01-4-4zM4 7V2a1.5 1.5 0 013 0"/></svg>2 Bath Rooms</div>
    <div><svg width="18" height="14" viewBox="0 0 18 14" fill="none" stroke="#f6a623" stroke-width="1.5"><rect x="1" y="1" width="16" height="12"/><path d="M1 10l5-4 4 3 3-2 4 3"/></svg>38 Pictures</div>
    <div><svg width="18" height="14" viewBox="0 0 18 14" fill="none" stroke="#f6a623" stroke-width="1.5"><rect x="1" y="1" width="16" height="12"/><path d="M5 5h8v5H5z"/></svg>2513 Sqft</div>
  </div>
  <a class="btn" href="#">Learn More</a>
</div>

<div class="abs city" role="img" aria-label="City skyline with high-rise towers"></div>

<section class="abs testimonials">
  <h2>WHAT OUR CLIENT SAYS ABOUT US...</h2>
  <svg class="arrow" style="left:42px" width="24" height="34" viewBox="0 0 24 34"><path d="M20 3L6 17l14 14" stroke="#fff" stroke-width="4" fill="none"/></svg>
  <svg class="arrow" style="left:1134px" width="24" height="34" viewBox="0 0 24 34"><path d="M4 3l14 14L4 31" stroke="#fff" stroke-width="4" fill="none"/></svg>

  <div class="quote-card" style="left:178px">
    <div class="avatar" role="img" aria-label="Client portrait"></div>
    <svg class="qm" width="34" height="28" viewBox="0 0 34 28" fill="#222"><path d="M0 28V16C0 7 5 1 13 0v5c-4 1-6 4-6 9h6v14zM20 28V16c0-9 5-15 13-16v5c-4 1-6 4-6 9h6v14z"/></svg>
    <p>Sed ut perspiciatis unde omnis iste natus sit voluptatem accusantium doloremque laudantium, totam rem aperiam,</p>
    <h5>John Doe</h5>
    <div class="stars">
      <svg width="92" height="16" viewBox="0 0 92 16" fill="#f6a623"><g id="st"><path d="M8 0l2.4 5 5.6.6-4.2 3.8 1.2 5.6L8 12.2 3 15l1.2-5.6L0 5.6 5.6 5z"/></g><use href="#st" x="19"/><use href="#st" x="38"/><use href="#st" x="57"/><use href="#st" x="76"/></svg>
    </div>
  </div>

  <div class="quote-card" style="left:667px">
    <div class="avatar" role="img" aria-label="Client portrait"></div>
    <svg class="qm" width="34" height="28" viewBox="0 0 34 28" fill="#222"><path d="M0 28V16C0 7 5 1 13 0v5c-4 1-6 4-6 9h6v14zM20 28V16c0-9 5-15 13-16v5c-4 1-6 4-6 9h6v14z"/></svg>
    <p>Sed ut perspiciatis unde omnis iste natus sit voluptatem accusantium doloremque laudantium, totam rem aperiam,</p>
    <h5>John Doe</h5>
    <div class="stars">
      <svg width="92" height="16" viewBox="0 0 92 16" fill="#f6a623"><use href="#st"/><use href="#st" x="19"/><use href="#st" x="38"/><use href="#st" x="57"/><use href="#st" x="76"/></svg>
    </div>
  </div>
</section>

<h2 class="abs centered sec-title blog-title">Latest <span>Blog</span></h2>

<article class="card post" style="left:110px">
  <div class="pic" role="img" aria-label="Modern white kitchen" style="background:linear-gradient(135deg,#f0f0ee,#b9b8b4 60%,#3a3a3a)"></div>
  <div class="date"><svg width="14" height="14" viewBox="0 0 14 14"><rect x="1" y="2" width="12" height="11" fill="none" stroke="#333" stroke-width="1.5"/><path d="M1 5h12M4 0v3M10 0v3" stroke="#333" stroke-width="1.5"/></svg>February 2, 2022</div>
  <h4>Lorem ipsum dolor sit amet,</h4>
  <p>Sed ut perspiciatis unde omnis iste natus sit voluptatem accusantium</p>
  <div class="readmore">READ MORE <svg width="14" height="14" viewBox="0 0 24 24"><circle cx="12" cy="12" r="11" fill="#f6a623"/><path d="M10 7l5 5-5 5" stroke="#fff" stroke-width="3" fill="none"/></svg></div>
</article>

<article class="card post" style="left:445px">
  <div class="pic" role="img" aria-label="Bathroom with freestanding bath and glass shower" style="background:linear-gradient(135deg,#6a6e72,#9ea3a6 55%,#2e3134)"></div>
  <div class="date"><svg width="14" height="14" viewBox="0 0 14 14"><rect x="1" y="2" width="12" height="11" fill="none" stroke="#333" stroke-width="1.5"/><path d="M1 5h12M4 0v3M10 0v3" stroke="#333" stroke-width="1.5"/></svg>February 2, 2022</div>
  <h4>Lorem ipsum dolor sit amet,</h4>
  <p>Sed ut perspiciatis unde omnis iste natus sit voluptatem accusantium</p>
  <div class="readmore">READ MORE <svg width="14" height="14" viewBox="0 0 24 24"><circle cx="12" cy="12" r="11" fill="#f6a623"/><path d="M10 7l5 5-5 5" stroke="#fff" stroke-width="3" fill="none"/></svg></div>
</article>

<article class="card post" style="left:778px">
  <div class="pic" role="img" aria-label="Bedroom with patterned bedding and window" style="background:linear-gradient(135deg,#d9d6d0,#b4aa9c 55%,#7b7a60)"></div>
  <div class="date"><svg width="14" height="14" viewBox="0 0 14 14"><rect x="1" y="2" width="12" height="11" fill="none" stroke="#333" stroke-width="1.5"/><path d="M1 5h12M4 0v3M10 0v3" stroke="#333" stroke-width="1.5"/></svg>February 2, 2022</div>
  <h4>Lorem ipsum dolor sit amet,</h4>
  <p>Sed ut perspiciatis unde omnis iste natus sit voluptatem accusantium</p>
  <div class="readmore">READ MORE <svg width="14" height="14" viewBox="0 0 24 24"><circle cx="12" cy="12" r="11" fill="#f6a623"/><path d="M10 7l5 5-5 5" stroke="#fff" stroke-width="3" fill="none"/></svg></div>
</article>

<footer class="abs footer">
  <svg class="footer-edge" width="1200" height="70" viewBox="0 0 1200 70">
    <polygon points="0,0 1200,0 1200,8 900,58 600,8 300,58 0,8" fill="#fff"/>
    <polygon points="80,12 300,52 520,12 300,32" fill="#f6a623"/>
    <polygon points="680,12 900,52 1120,12 900,32" fill="#f6a623"/>
  </svg>
  <div class="fcol" style="left:110px">
    <h6>Quick Links</h6>
    <ul><li>Home</li><li>Counseling</li><li>Buprenorphine Therapy</li><li>About Us</li><li>Contact Us</li></ul>
  </div>
  <div class="fcol" style="left:325px">
    <h6>Company</h6>
    <ul><li>Terms &amp; Conditions</li><li>Privacy</li><li>Complaint Handling</li><li>Due Diligence Checklist</li><li>Sitemap</li></ul>
  </div>
  <div class="fcol contact" style="left:545px">
    <h6>Contact Us</h6>
    <ul>
      <li><svg width="12" height="12" viewBox="0 0 24 24"><path d="M6.6 10.8a15 15 0 006.6 6.6l2.2-2.2a1 1 0 011-.25 11.4 11.4 0 003.6.57 1 1 0 011 1V20a1 1 0 01-1 1A17 17 0 013 4a1 1 0 011-1h3.5a1 1 0 011 1 11.4 11.4 0 00.57 3.6 1 1 0 01-.25 1z" fill="#fff"/></svg>02 6155 0192</li>
      <li><svg width="12" height="12" viewBox="0 0 24 24"><rect x="2" y="5" width="20" height="14" fill="#fff"/><path d="M2 5l10 8 10-8" stroke="#22252e" stroke-width="2" fill="none"/></svg>info@ferndaleestatecollective.com.au</li>
      <li><svg width="12" height="14" viewBox="0 0 10 14"><path d="M5 0a5 5 0 015 5c0 4-5 9-5 9S0 9 0 5a5 5 0 015-5z" fill="#fff"/><circle cx="5" cy="5" r="2" fill="#22252e"/></svg>118/4 Harper Crescent, Gungahlin,<br>ACT, 2912</li>
      <li><svg width="12" height="12" viewBox="0 0 24 24"><rect x="2" y="8" width="20" height="12" fill="#fff"/><rect x="6" y="2" width="12" height="6" fill="#fff"/></svg>02 6155 0193</li>
    </ul>
  </div>
  <div class="fcol" style="left:832px">
    <h6>Subscribe to our Blog</h6>
    <p class="lead">Sign up today to get resources on how to attract and retain more customers!</p>
    <div class="sub-form"><span>✉ Email Address</span><span class="go"><svg width="14" height="14" viewBox="0 0 24 24"><path d="M2 12L22 3l-6 19-4-8z" fill="#fff"/></svg></span></div>
    <div class="fsoc"><span></span><span class="o"></span><span></span><span></span></div>
  </div>
</footer>

<div class="abs bottom-bar">
  <div class="l">Copyright© 2021 <u>ferndaleestatecollective.com.au</u> | All Rights Reserved</div>
  <div class="r">Terms and Conditions &nbsp;|&nbsp; Privacy Policy</div>
</div>

</body>
</html>
```